We are a recruitment company based in Norwich/Cambridge England.
I have included our company logo which we want to remain the same.

What we are looking for is a new creative Business card which will really stand out!!

Contact Information for Business Card

Harriet Dunmore
email: Harriet@plavex.co.uk
Address: Brackwell House
Fenmoor Enterprise Park
Partridge Way
Norwich
QB9 3KX
Tel:01632 960418

```html
<!DOCTYPE html>
<html lang="en">
<head>
<meta charset="utf-8">
<title>Plavex Business Card</title>
<link rel="stylesheet" href="https://fonts.googleapis.com/css2?family=Jost:wght@400;500;600&display=swap">
<style>
  :root {
    --backdrop: #2b2b2c;
    --card: #1d1d1e;
    --card-edge: #252526;
    --green: #7cc242;
    --grey: #9a9a9c;
    --grey-dark: #3a3a3b;
    --white: #f2f2f2;
    --muted: #bdbdbd;
  }
  * { margin: 0; padding: 0; box-sizing: border-box; }
  html, body { width: 1200px; height: 900px; overflow: hidden; }
  body {
    background: radial-gradient(ellipse at 70% 20%, #3a3a3b 0%, var(--backdrop) 60%, #1f1f20 100%);
    font-family: "Jost", sans-serif;
    position: relative;
  }
  .card {
    position: absolute;
    left: 250px;
    width: 700px;
    height: 400px;
    background: var(--card);
    border: 1px solid var(--card-edge);
    box-shadow: 0 18px 40px rgba(0,0,0,0.55);
  }
  .card--back { top: 32px; }
  .card--front { top: 466px; }

  /* Back */
  .back-brand {
    position: absolute;
    top: 150px; left: 0; right: 0;
    display: flex; justify-content: center; align-items: center; gap: 18px;
  }
  .brand-dot {
    width: 58px; height: 58px; border-radius: 50%;
    background: var(--grey-dark);
  }
  .brand-name {
    font-weight: 500; font-size: 52px; line-height: 1; color: var(--grey-dark);
  }
  .brand-tagline {
    font-size: 10px; letter-spacing: 4px; color: #5b5b5c; margin-top: 6px;
  }
  .back-url {
    position: absolute; bottom: 36px; left: 0; right: 0;
    text-align: center; font-size: 15px; letter-spacing: 4px; color: var(--muted);
  }
  .back-url .accent { color: var(--green); }

  /* Front */
  .front-brand {
    position: absolute; left: 46px; top: 150px;
    display: flex; align-items: center; gap: 16px;
  }
  .front-brand .brand-dot { width: 72px; height: 72px; background: var(--green); }
  .front-brand .brand-name { color: var(--grey); font-size: 60px; }
  .front-brand .brand-tagline { color: var(--grey); letter-spacing: 5px; }

  .contact {
    position: absolute; left: 370px; top: 70px; right: 30px;
  }
  .contact__head {
    border-left: 2px solid var(--green);
    padding-left: 18px; padding-bottom: 4px;
  }
  .contact__name { font-weight: 600; font-size: 36px; color: var(--grey); line-height: 1.1; }
  .contact__role { font-weight: 500; font-size: 20px; color: var(--green); letter-spacing: 1px; }
  .contact__body {
    border-left: 2px solid var(--white);
    padding-left: 18px; margin-top: 16px;
    font-size: 16px; color: var(--white); line-height: 1.35;
  }
  .contact__address { margin-bottom: 10px; }
  .contact__line { display: flex; align-items: center; gap: 10px; font-size: 18px; line-height: 1.5; }
  .contact__line svg { width: 18px; height: 18px; flex: none; }
  .contact__line .accent { color: var(--green); }
</style>
</head>
<body>
  <section class="card card--back">
    <div class="back-brand">
      <span class="brand-dot"></span>
      <div>
        <div class="brand-name">Plavex</div>
        <div class="brand-tagline">Technology Recruitment</div>
      </div>
    </div>
    <div class="back-url">www.<span class="accent">plavexrecruit</span>.com</div>
  </section>

  <section class="card card--front">
    <div class="front-brand">
      <span class="brand-dot"></span>
      <div>
        <div class="brand-name">Plavex</div>
        <div class="brand-tagline">Technology Recruitment</div>
      </div>
    </div>

    <div class="contact">
      <div class="contact__head">
        <div class="contact__name">Harriet Dunmore</div>
        <div class="contact__role">CEO &amp; FOUNDER</div>
      </div>
      <div class="contact__body">
        <p class="contact__address">Brackwell House Fenmoor Enterprise Park,<br>Partridge Way Norwich, QB9 3KX</p>
        <p class="contact__line">
          <svg viewBox="0 0 24 24" aria-hidden="true"><path fill="#7cc242" d="M6.6 10.8a15 15 0 0 0 6.6 6.6l2.2-2.2c.3-.3.7-.4 1-.2 1.1.4 2.3.6 3.6.6.6 0 1 .4 1 1V20c0 .6-.4 1-1 1A17 17 0 0 1 3 4c0-.6.4-1 1-1h3.5c.6 0 1 .4 1 1 0 1.3.2 2.5.6 3.6.1.3 0 .7-.2 1z"/></svg>
          01632 960418
        </p>
        <p class="contact__line">
          <svg viewBox="0 0 24 24" aria-hidden="true"><rect x="2" y="5" width="20" height="14" rx="1" fill="#7cc242"/><path d="M2 6l10 7 10-7" stroke="#1d1d1e" stroke-width="2" fill="none"/></svg>
          Harriet@plavex.co.uk
        </p>
        <p class="contact__line">
          <svg viewBox="0 0 24 24" aria-hidden="true"><circle cx="13" cy="10" r="7" stroke="#7cc242" stroke-width="2.5" fill="none"/><path d="M8 15l-5 5" stroke="#7cc242" stroke-width="2.5"/></svg>
          <span>www.<span class="accent">plavexrecruit</span>.com</span>
        </p>
      </div>
    </div>
  </section>
</body>
</html>
```